Kestrada LLC, needs a web page no more than 5 pages (for now)

Kestrada is a general contractor. Our services include general contracting, design-build construction, disaster recovery and environmental remediation. Our main clients are PMX, TQ, State and Local Gov't Agencies, Hospitals and Schools. Kestrada is also a SDVOSB.

```html
<!DOCTYPE html>
<html lang="en">
<head>
<meta charset="utf-8">
<title>Kestrada — General Contractor</title>
<link href="https://fonts.googleapis.com/css2?family=Roboto:wght@400;500;600;700&display=swap" rel="stylesheet">
<style>
:root{
  --bg:#f4f2f0;
  --ink:#1d1c1a;
  --muted:#4a4744;
  --gold:#b27a35;
  --gold-2:#d6a760;
  --line:#d9d4cf;
  --white:#ffffff;
  --dark:#252220;
}
*{box-sizing:border-box;margin:0;padding:0}
html,body{width:1200px;height:4005px;overflow:hidden}
body{background:var(--bg);font-family:'Roboto',sans-serif;color:var(--ink);position:relative}
.abs{position:absolute}
a{color:inherit;text-decoration:none}

.brand{font-size:26px;font-weight:600;color:var(--gold);display:flex;align-items:center;gap:10px}
.brand .mark{width:18px;height:18px;border-radius:50%;background:var(--gold)}

.nav-link{top:36px;font-size:16px;color:var(--muted)}
.nav-link.active{color:var(--gold);font-weight:600}
.btn{display:flex;align-items:center;gap:12px;background:var(--gold);color:var(--white);border-radius:30px;font-size:16px;padding:0 16px 0 6px}
.btn .dot{width:26px;height:26px;border-radius:50%;background:var(--white);display:flex;align-items:center;justify-content:center}

.hero{left:73px;top:101px;width:1054px;height:497px;border-radius:46px;overflow:hidden;
  background:linear-gradient(100deg,#e8ecf0 0%,#d6dfe7 35%,#a9b9c6 60%,#7f8e98 80%,#b7a27a 100%)}
.hero h1{left:39px;top:124px;font-size:43px;font-weight:500;line-height:56px;color:var(--ink)}
.hero h1 span{color:var(--gold);font-weight:600}
.hero p{left:39px;top:250px;width:500px;font-size:16px;line-height:26px;color:var(--muted)}

.photo{border-radius:22px}
.pill{border:1px solid var(--gold);color:var(--gold);border-radius:20px;font-size:16px;display:flex;align-items:center;justify-content:center;letter-spacing:.5px;background:transparent}
.about h2{font-size:34px;font-weight:500;line-height:43px}
.stat-num{font-size:33px;font-weight:500}
.stat-label{font-size:15px;color:var(--muted)}
.divider{width:1px;height:54px;background:var(--line)}

.partner{top:1176px;height:50px;display:flex;align-items:center;gap:10px;font-size:20px;font-weight:600;color:#a9a5a1;transform:translateX(-50%);white-space:nowrap}
.partner .sq{width:26px;height:26px;background:#c4c0bb}
.partner.on{color:var(--ink)}
.partner.on .sq{background:var(--gold)}

.services{left:73px;top:1333px;width:1054px;height:1099px;background:var(--white);border-radius:22px}
.sec-title{font-size:34px;font-weight:500;text-align:center;width:100%}
.svc{left:25px;width:1004px;height:197px;border-bottom:1px solid var(--line)}
.svc .num{left:31px;top:80px;font-size:22px;color:var(--gold)}
.svc .name{left:82px;top:78px;font-size:23px;line-height:33px}
.svc .desc{left:611px;top:74px;width:290px;font-size:16px;line-height:26px;color:var(--muted)}
.svc .go{left:935px;top:82px;width:38px;height:38px;border-radius:50%;background:var(--gold);display:flex;align-items:center;justify-content:center}
.svc.feature{top:247px;height:173px;border-radius:20px;border:none;background:linear-gradient(90deg,#b27a35,#d4a660)}
.svc.feature .num,.svc.feature .name,.svc.feature .desc{color:var(--white);top:54px}
.svc.feature .num{top:56px}
.svc.feature .name{font-weight:500;top:50px}
.svc.feature .desc{top:46px}
.svc.feature .go{background:var(--white);top:68px}

.card{top:2657px;width:331px;height:415px;border-radius:20px;overflow:hidden}
.card .label{left:26px;bottom:28px;font-size:19px;font-weight:600;color:var(--white)}
.round{width:48px;height:48px;border-radius:50%;background:var(--gold);display:flex;align-items:center;justify-content:center}

.review{top:3291px;width:231px;height:304px;background:var(--white);border:1px solid var(--line);border-radius:14px;padding:36px 20px 0}
.stars{color:#f09a1a;font-size:16px;letter-spacing:1px}
.review p{margin-top:16px;font-size:15px;line-height:26px;color:var(--muted)}
.who{display:flex;align-items:center;gap:12px;margin-top:22px}
.avatar{width:50px;height:50px;border-radius:50%;background:var(--gold);color:var(--white);font-size:22px;display:flex;align-items:center;justify-content:center}
.who b{font-size:15px;font-weight:500;display:block}
.who small{font-size:11px;color:var(--muted)}

.footer{left:0;top:3727px;width:1200px;height:278px;background:var(--dark);border-radius:44px 44px 0 0;color:var(--white)}
.footer .nav{top:178px;font-size:18px}
</style>
</head>
<body>

<!-- header -->
<a class="abs brand" style="left:73px;top:30px"><span class="mark"></span>Kestrada</a>
<a class="abs nav-link active" style="left:580px">Home</a>
<a class="abs nav-link" style="left:666px">About Us</a>
<a class="abs nav-link" style="left:774px">Services</a>
<a class="abs nav-link" style="left:877px">Projects</a>
<a class="abs btn" style="left:977px;top:28px;height:37px"><span class="dot"><svg width="14" height="14" viewBox="0 0 14 14"><path d="M2 7h10M8 3l4 4-4 4" stroke="#b27a35" stroke-width="1.8" fill="none"/></svg></span>Contact Us</a>

<!-- hero -->
<section class="abs hero">
  <div class="abs" role="img" aria-label="High-rise building under construction with tower cranes against a cloudy sky" style="left:480px;top:0;width:574px;height:497px;background:linear-gradient(180deg,rgba(150,170,185,.3),rgba(110,120,110,.55) 60%,rgba(170,150,100,.7))"></div>
  <h1 class="abs">Building with Integrity as<br>a <span>Certified SDVOSB</span></h1>
  <p class="abs">Partner with a certified SDVOSB committed to integrity, service, and results in construction solutions.</p>
  <a class="abs btn" style="left:39px;top:326px;height:36px;width:218px">
    <span class="dot"><svg width="14" height="14" viewBox="0 0 14 14"><path d="M2 7h10M8 3l4 4-4 4" stroke="#b27a35" stroke-width="1.8" fill="none"/></svg></span>Explore Our Services</a>
</section>

<!-- about -->
<section class="about">
  <div class="abs photo" role="img" aria-label="Site engineer in a hard hat reviewing building plans" style="left:73px;top:684px;width:269px;height:410px;background:linear-gradient(160deg,#7a8a93,#5d5448 60%,#a08a68)"></div>
  <div class="abs photo" role="img" aria-label="Gloved hand picking up a plastic bottle on a beach cleanup" style="left:850px;top:684px;width:277px;height:292px;background:linear-gradient(170deg,#6f8fa8,#9fb0bb 45%,#b99b7d)"></div>
  <div class="abs pill" style="left:385px;top:696px;width:128px;height:30px">ABOUT US</div>
  <h2 class="abs" style="left:385px;top:744px">Proven SDVOSB Partner<br>You Can Trust</h2>
  <p class="abs" style="left:385px;top:843px;width:420px;font-size:15px;line-height:26px;color:var(--muted)">Sed ut perspiciatis unde omnis iste natus error sit voluptatem accusantium doloremque laudantium, totam rem aperiam</p>
  <a class="abs btn" style="left:385px;top:940px;height:36px;width:151px"><span class="dot"><svg width="14" height="14" viewBox="0 0 14 14"><path d="M2 7h10M8 3l4 4-4 4" stroke="#b27a35" stroke-width="1.8" fill="none"/></svg></span>Know More</a>

  <div class="abs" style="left:385px;top:1008px"><div class="stat-num">25+</div><div class="stat-label">Completed Projects</div></div>
  <div class="abs divider" style="left:552px;top:1018px"></div>
  <div class="abs" style="left:580px;top:1010px"><div class="stat-num">50+</div><div class="stat-label">Trusted Partners</div></div>
  <div class="abs divider" style="left:724px;top:1018px"></div>
  <div class="abs" style="left:752px;top:1008px"><div class="stat-num">95k</div><div class="stat-label">Happy Clients</div></div>
  <div class="abs divider" style="left:878px;top:1018px"></div>
  <div class="abs" style="left:907px;top:1010px"><div class="stat-num">300+</div><div class="stat-label">Works Delivered</div></div>
</section>

<!-- partners -->
<div class="abs partner" style="left:73px"><span class="sq"></span>Ostrava Group</div>
<div class="abs partner on" style="left:328px"><span class="sq"></span>Granite Line</div>
<div class="abs partner" style="left:584px"><span class="sq"></span>Halden Works</div>
<div class="abs partner" style="left:782px"><span class="sq"></span>Brookmere</div>
<div class="abs partner" style="left:973px"><span class="sq"></span>Tallis Build</div>
<div class="abs partner" style="left:1180px"><span class="sq"></span>Ostrava Group</div>

<!-- services -->
<section class="abs services">
  <div class="abs pill" style="left:434px;top:87px;width:186px;height:32px">OUR SERVICES</div>
  <h2 class="abs sec-title" style="top:136px">See What We Offer You</h2>

  <div class="abs svc feature">
    <span class="abs num">01.</span>
    <span class="abs name">General<br>Contracting</span>
    <span class="abs desc">Sed ut perspiciatis unde omnis iste nat error sit voluptatem accu santium dolo remque laudantium</span>
    <span class="abs go"><svg width="14" height="14" viewBox="0 0 14 14"><path d="M2 7h10M8 3l4 4-4 4" stroke="#b27a35" stroke-width="1.8" fill="none"/></svg></span>
  </div>
  <div class="abs" role="img" aria-label="Contractor on a job site checking his phone" style="left:287px;top:220px;width:290px;height:230px;border-radius:12px;transform:rotate(-10deg);background:linear-gradient(135deg,#c79a6a,#3d4650 55%,#c9c7c2);border:4px solid var(--white)"></div>

  <div class="abs svc" style="top:420px">
    <span class="abs num">02.</span><span class="abs name">Design-Build<br>Construction</span>
    <span class="abs desc">Sed ut perspiciatis unde omnis iste nat error sit voluptatem accu santium dolo remque laudantium</span>
    <span class="abs go"><svg width="14" height="14" viewBox="0 0 14 14"><path d="M4 10l6-6M5 4h5v5" stroke="#fff" stroke-width="1.8" fill="none"/></svg></span>
  </div>
  <div class="abs svc" style="top:617px">
    <span class="abs num">03.</span><span class="abs name">Disaster<br>Recovery</span>
    <span class="abs desc">Sed ut perspiciatis unde omnis iste nat error sit voluptatem accu santium dolo remque laudantium</span>
    <span class="abs go"><svg width="14" height="14" viewBox="0 0 14 14"><path d="M4 10l6-6M5 4h5v5" stroke="#fff" stroke-width="1.8" fill="none"/></svg></span>
  </div>
  <div class="abs svc" style="top:815px">
    <span class="abs num">04.</span><span class="abs name">Environmental<br>Remediation</span>
    <span class="abs desc">Sed ut perspiciatis unde omnis iste nat error sit voluptatem accusantium dolo remque laudantium</span>
    <span class="abs go"><svg width="14" height="14" viewBox="0 0 14 14"><path d="M4 10l6-6M5 4h5v5" stroke="#fff" stroke-width="1.8" fill="none"/></svg></span>
  </div>
</section>

<!-- projects -->
<div class="abs pill" style="left:73px;top:2519px;width:187px;height:30px">OUR PROJECTS</div>
<h2 class="abs" style="left:73px;top:2568px;font-size:34px;font-weight:500">Design Through Vision</h2>
<div class="abs round" style="left:1009px;top:2554px"><svg width="18" height="18" viewBox="0 0 18 18"><path d="M15 9H3M7 5L3 9l4 4" stroke="#fff" stroke-width="2" fill="none"/></svg></div>
<div class="abs round" style="left:1079px;top:2554px"><svg width="18" height="18" viewBox="0 0 18 18"><path d="M3 9h12M11 5l4 4-4 4" stroke="#fff" stroke-width="2" fill="none"/></svg></div>

<div class="abs card" role="img" aria-label="Multi-storey building wrapped in scaffolding" style="left:73px;background:linear-gradient(170deg,#6f9bc4,#8a7a66 55%,#a9744a)"></div>
<div class="abs card" style="left:435px;top:2696px;height:376px;background:linear-gradient(170deg,#4d4a44,#6b5a48 50%,#8e8a80)" role="img" aria-label="Crew in safety vests stacking sandbags after a flood">
  <div class="abs" style="left:145px;top:170px;width:38px;height:38px;border-radius:50%;background:var(--gold);display:flex;align-items:center;justify-content:center"><svg width="14" height="14" viewBox="0 0 14 14"><path d="M2 7h10M8 3l4 4-4 4" stroke="#fff" stroke-width="1.8" fill="none"/></svg></div>
  <span class="abs label">Disaster Recovery</span>
</div>
<div class="abs card" role="img" aria-label="Litter picker lifting a plastic bottle out of a green lake" style="left:796px;background:linear-gradient(170deg,#5f8a5a,#3f7c7a 50%,#7fa9a6)"></div>

<!-- testimonials -->
<div class="abs pill" style="left:451px;top:3161px;width:298px;height:30px">TRUST THROUGH OUR WORK</div>
<h2 class="abs sec-title" style="left:0;top:3210px">We Deliver Quality Services</h2>

<div class="abs review" style="left:112px"><div class="stars">★★★★★</div><p>Sed ut perspiciatis unde omnis iste nat error sit volu ptatem accu santium dolo remque laudantium totm rem aperiam</p><div class="who"><span class="avatar">DW</span><span><b>Dana Whitlow</b><small>Fresno, CA</small></span></div></div>
<div class="abs review" style="left:373px"><div class="stars">★★★★★</div><p>Sed ut perspiciatis unde omnis iste nat error sit volu ptatem accu santium dolo remque laudantium totm rem aperiam</p><div class="who"><span class="avatar">DW</span><span><b>Dana Whitlow</b><small>Fresno, CA</small></span></div></div>
<div class="abs review" style="left:634px"><div class="stars">★★★★★</div><p>Sed ut perspiciatis unde omnis iste nat error sit volu ptatem accu santium dolo remque laudantium totm rem aperiam</p><div class="who"><span class="avatar">DW</span><span><b>Dana Whitlow</b><small>Fresno, CA</small></span></div></div>
<div class="abs review" style="left:896px"><div class="stars">★★★★★</div><p>Sed ut perspiciatis unde omnis iste nat error sit volu ptatem accu santium dolo remque laudantium totm rem aperiam</p><div class="who"><span class="avatar">DW</span><span><b>Dana Whitlow</b><small>Fresno, CA</small></span></div></div>

<svg class="abs" style="left:562px;top:3624px" width="76" height="16" viewBox="0 0 76 16">
  <circle cx="8" cy="8" r="7" fill="#b27a35"/><circle cx="31" cy="8" r="5" fill="#555"/><circle cx="51" cy="8" r="5" fill="#555"/><circle cx="71" cy="8" r="5" fill="#555"/>
</svg>

<!-- footer -->
<footer class="abs footer">
  <div class="abs brand" style="left:0;width:1200px;top:92px;justify-content:center;font-size:30px"><span class="mark"></span>Kestrada</div>
  <a class="abs nav" style="left:311px">Home</a>
  <a class="abs nav" style="left:416px">About Us</a>
  <a class="abs nav" style="left:547px">Services</a>
  <a class="abs nav" style="left:671px">Projects</a>
  <a class="abs nav" style="left:795px">Contact Us</a>
  <div class="abs" style="left:112px;top:225px;width:976px;height:1px;background:var(--gold)"></div>
  <div class="abs" style="left:0;top:239px;width:1200px;text-align:center;font-size:13px">Copyright © 2025 Kestrada. All rights reserved.</div>
</footer>

</body>
</html>
```